www.lanternmerow.net

Hi,
UPDATE: Logo attached
TAG LINE NEW: OBITUARIES * CONDOLENCE NOTES
MULTIMEDIA MEMORIAL
Please refer to our existing site for more explanation of who we are?
We are a global data collecting portal site managing the Jewish funeral industry where users:
a) family and freinds in grief or "ancestry" searching persons
b) chevra kadisha's (funeral parlor)
c) current and historic cemetaries
d) Jewish Media Partners
arrive and choose a function (category):
in order to:
- upload a basic listing (FREE)
- upload/upgrade a multimedia listing (PAID)
- or search for a listing
of a deceased person (potentially millions of entries)
The functions (or categories) are accessed after the user:
Chooses their global location of search by
"Choose your Location" ie: Australia/NZ (which country?)
and allows the USER to choose a category function such as:
GROUP A (Local Info) GROUP B (Soul Search)
Chevra Kadisha Funerals (within 7 days)
Cemetaries Recently Deceased (up to 12mth)
Stonemasons Soul Search (after 1 year)
Jewish Media Partners
GROUP C (Jewish Death & Mourning Customs)
The way of Jewish burial
3000 y/old customs
When will Moshiach Come ?
Will I see my loved one again?
AIM:
To utilize existing logo and side menus (Member, Main & Resources) to create a user freindly and simpler friendly landing page, warmer and more softer for viewers.
To create logo buttons for the service catogories:
A, B & C and separate sub catagories
The MAIN AIM is to offer users opportunity to upload (LOG-IN required)
a) NEW basic FREE listing
b) NEW Multi-media PAID listing
SUMMARY:
1) User arrives at landing paid and sees global map, where he/she must choose the location in order to localize his data search
At this point, he/she can see what the site offers by the side MAIN, menu and icon function/catagories
(ie: Soul Search, New Basic Listing, Multimedia Listing)
2) After arriving at location (ie: Australia/NZ), the user then chooses the sub-function icon:
A- Local Funeral Service Info (Chevra Kadisha, Cemetary etc)
B- Soul Search (Funeral,Recently Deceased, Soul Search)
C- Jewish Death & Mourning Cutoms
Updates
Hi
Reason: Because of the holidays, we are happy to extend the deadline....
happy times
Target Market(s)
Family persons (Guest Member) & Industry (Members)
Industry/Entity Type
Industry
Requirements
Must have
- Style : Simple, Neat & Easy to Navigate
Icons: for each catagory/function
Colors; natural
-
Ability to bring inspiration, hope, light and healing to a difficult subject matter. (site look)
-
Education a profoundly deep 3000 y/old historically rich and mystic tradition to a wide audience
-
Allow children to access and upload data about grandparents etc
-
To promote on landing page the Invitation of local Chevra Kadisha's (funeral parlors), who have no web exposure, to get involved and LOG-IN and upload basic or multimedia listings.
(ie: please Register your local Chevra Kadisha here)
-
To promote on the landing page sample listings (Recently Deceased), to show look/feel of listings

```html
<!DOCTYPE html>
<html lang="en">
<head>
<meta charset="utf-8">
<title>LanternMerow.net – Obituaries, Condolence Notes, Multimedia Memorial</title>
<link href="https://fonts.googleapis.com/css2?family=Cormorant+Garamond:wght@400;500;600&family=Open+Sans:wght@400;600&display=swap" rel="stylesheet">
<style>
  :root{
    --orange:#f39a2a;
    --orange-dark:#d9771a;
    --ink:#2b2b2b;
    --text:#333333;
    --muted:#888888;
    --panel:#3b3b3b;
    --line:#d2d2d2;
    --white:#ffffff;
    --serif:"Cormorant Garamond", Georgia, serif;
    --sans:"Open Sans", Arial, sans-serif;
  }
  *{box-sizing:border-box;margin:0;padding:0}
  html,body{width:1200px;height:1176px;overflow:hidden;background:var(--white)}
  body{position:relative;font-family:var(--sans);color:var(--text)}
  a{color:inherit;text-decoration:none}

  /* Header */
  .brand{position:absolute;left:62px;top:8px;width:200px;height:150px}
  .brand-name{position:absolute;left:0;top:74px;font-family:var(--serif);font-size:25px;font-weight:500;color:var(--ink);letter-spacing:.2px;white-space:nowrap}
  .brand-rule{position:absolute;left:2px;top:106px;width:186px;height:2px;background:var(--ink)}
  .brand-region{position:absolute;right:12px;top:126px;font-family:var(--sans);font-size:14px;color:var(--ink)}

  .login{position:absolute;left:978px;top:28px;width:222px;height:154px;background:var(--panel);border-radius:0 0 0 8px;z-index:10}
  .login-tab{position:absolute;left:1079px;top:0;width:85px;height:34px;background:var(--orange-dark);color:var(--white);font-family:var(--serif);font-size:25px;text-align:center;line-height:30px;z-index:11}
  .login-tab::after{content:"";position:absolute;left:36px;bottom:-7px;border:7px solid transparent;border-bottom:0;border-top-color:var(--orange-dark)}
  .login-field{position:absolute;left:24px;width:181px;height:29px;border-radius:14px;background:linear-gradient(#f6f6f6,#dcdcdc);font-size:14px;color:#6a6a6a;padding-left:20px;line-height:29px}
  .login-field.user{top:20px}
  .login-field.pass{top:56px}
  .login-submit{position:absolute;left:78px;top:93px;width:79px;height:28px;border-radius:14px;background:linear-gradient(#ffc25c,var(--orange-dark));color:var(--white);font-family:var(--serif);font-size:22px;text-align:center;line-height:26px}
  .login-note{position:absolute;left:0;top:128px;width:222px;text-align:center;font-size:11.5px;line-height:16px;color:#e9e9e9;white-space:nowrap}

  /* Main navigation */
  .main-nav{position:absolute;left:0;top:168px;width:1200px;height:40px;background:linear-gradient(#f2f2f2,#dedede);border-top:1px solid #e9e9e9}
  .main-nav a{position:absolute;top:0;height:40px;line-height:40px;font-family:var(--serif);font-size:22px;color:#444}
  .main-nav .is-active{left:254px;width:86px;text-align:center;background:linear-gradient(#ffb75c,var(--orange));box-shadow:inset 0 0 10px rgba(255,255,255,.4)}
  .nav-local{left:383px}.nav-soul{left:623px}.nav-customs{left:785px}

  .dropdown{position:absolute;left:254px;top:209px;width:173px;height:215px;background:rgba(110,110,110,.88);z-index:5;padding-top:15px}
  .dropdown a{display:block;height:36px;line-height:36px;padding-left:30px;font-size:15px;color:var(--white)}
  .dropdown a.is-current{background:#3e3e3e;height:26px;line-height:26px;margin-bottom:5px}

  /* Slider */
  .slider{position:absolute;left:42px;top:222px;width:1128px;height:414px;background:var(--white);box-shadow:0 14px 22px -12px rgba(0,0,0,.45),0 0 10px rgba(0,0,0,.08)}
  .slider-image{position:absolute;left:5px;top:0;width:1118px;height:365px;border-radius:8px;background:radial-gradient(ellipse at 55% 45%,#e9a24a 0%,#c56a1c 30%,#8d4a1a 55%,#d9c9b2 80%,#efe6d6 100%)}
  .slider-caption{position:absolute;left:0;top:368px;width:100%;text-align:center;font-family:var(--serif);font-size:27px;color:var(--ink);letter-spacing:.5px}
  .slider-arrow{position:absolute;top:407px;width:47px;height:47px;border-radius:6px;background:linear-gradient(#c9671a,#9c4a0e);z-index:4}
  .slider-arrow svg{display:block;margin:14px auto}
  .slider-arrow.prev{left:37px}.slider-arrow.next{left:1127px}

  /* Feature columns */
  .feature{position:absolute;top:686px;height:270px}
  .feature h2{font-family:var(--serif);font-weight:500;font-size:27px;color:var(--ink);letter-spacing:.4px;white-space:nowrap}
  .feature p{font-size:13.5px;line-height:21.5px;color:var(--ink)}
  .feature .icon,.feature .lead{position:absolute}
  .region{left:54px;width:340px}
  .listing{left:448px;width:332px}
  .passings{left:828px;width:342px}
  .divider{position:absolute;top:706px;width:1px;height:250px;background:var(--line)}
  .divider.one{left:405px}.divider.two{left:801px}

  .read-more{position:absolute;width:97px;height:27px;border-radius:6px;background:#dcdcdc;color:#8a8a8a;font-size:14px;text-align:center;line-height:27px}
  .register-now{position:absolute;left:37px;top:206px;width:248px;height:40px;border-radius:6px;background:linear-gradient(#ffc266,var(--orange));border:1px solid var(--orange-dark);font-size:26px;color:var(--ink);text-align:center;line-height:38px}

  /* Partners */
  .partners{position:absolute;left:0;top:980px;width:1200px;height:88px;background:linear-gradient(#e4e4e4,#f7f7f7 50%,#e9e9e9)}
  .partner{position:absolute;top:0;height:88px;line-height:88px;font-family:var(--serif);font-weight:600;font-size:20px;color:#222;white-space:nowrap}

  /* Footer */
  .footer-nav{position:absolute;left:0;top:1074px;width:1200px;height:50px;border-bottom:2px solid #e2e2e2;background:linear-gradient(#f1f1f1,#fff)}
  .footer-nav a{position:absolute;top:0;line-height:50px;font-family:var(--serif);font-size:21px;color:#444}
  .copyright{position:absolute;left:7px;top:1140px;font-size:13px;color:var(--muted)}
  .social{position:absolute;right:22px;top:1139px;display:flex;gap:14px;font-size:13px;color:#555}
  .social a{display:flex;align-items:center;gap:5px}
  .social i{display:block;width:10px;height:10px;background:#7b8ba3;border-radius:2px}
</style>
</head>
<body>

<header>
  <a class="brand" href="#">
    <span class="brand-name">LanternMerow.net</span>
    <span class="brand-rule"></span>
    <span class="brand-region">Australia</span>
  </a>

  <div class="login-tab">Login</div>
  <form class="login">
    <div class="login-field user">Username</div>
    <div class="login-field pass">Password</div>
    <div class="login-submit">Sign in</div>
    <div class="login-note">Please Register a Memorial Page Here</div>
  </form>
</header>

<nav class="main-nav">
  <a class="is-active" href="#">Home</a>
  <a class="nav-local" href="#">Local Information</a>
  <a class="nav-soul" href="#">Soul Search</a>
  <a class="nav-customs" href="#">Jewish Customs</a>
</nav>
<div class="dropdown">
  <a class="is-current" href="#">Our mission</a>
  <a href="#">About Us</a>
  <a href="#">Personal Media</a>
  <a href="#">Contact Us</a>
  <a href="#">On-line Forum</a>
</div>

<section class="slider">
  <div class="slider-image" role="img" aria-label="Golden Star of David resting on a page of Hebrew text"></div>
  <p class="slider-caption">Welcome to the global Chevra Kadisha network</p>
</section>
<a class="slider-arrow prev" href="#" aria-label="Previous slide"><svg width="16" height="19" viewBox="0 0 16 19"><path d="M15 1 L1 9.5 L15 18 Z" fill="#fff"/></svg></a>
<a class="slider-arrow next" href="#" aria-label="Next slide"><svg width="16" height="19" viewBox="0 0 16 19"><path d="M1 1 L15 9.5 L1 18 Z" fill="#fff"/></svg></a>

<section class="feature region">
  <h2>Choose Your Region</h2>
  <div class="icon" role="img" aria-label="Map of Australia" style="left:0;top:82px;width:78px;height:60px;background:#6a6a6a;border-radius:40% 45% 50% 35%"></div>
  <p class="lead" style="left:88px;top:68px;width:252px">Lorem Ipsum is simply dummy text of the printing and typesetting industry. Lorem Ipsum has been the industry's standard dummy text ever</p>
  <p class="lead" style="left:8px;top:164px;width:332px">Lorem Ipsum is simply dummy text of the printing and typesetting industry. Lorem Ipsum has been the industry's standard dummy text ever</p>
  <a class="read-more" href="#" style="left:234px;top:236px">Read more...</a>
</section>
<div class="divider one"></div>

<section class="feature listing">
  <h2>Register or Update a listing</h2>
  <div class="icon" role="img" aria-label="Illustration of a man in a suit" style="left:2px;top:70px;width:64px;height:90px;background:linear-gradient(#8a7460,#3d3d3d);border-radius:30px 30px 8px 8px"></div>
  <p class="lead" style="left:82px;top:70px;width:250px">Lorem Ipsum is simply dummy text of the printing and typesetting industry. Lorem Ipsum has been the industry's standard dummy text ever</p>
  <a class="register-now" href="#">Register Now</a>
</section>
<div class="divider two"></div>

<section class="feature passings">
  <h2 style="margin-top:6px">Recent Passings</h2>
  <div class="icon" role="img" aria-label="Pair of footprints" style="left:0;top:62px;width:70px;height:92px;background:#1e1e1e;border-radius:40%"></div>
  <p class="lead" style="left:79px;top:62px;width:250px">Lorem Ipsum is simply dummy text of the printing and typesetting industry. Lorem Ipsum has been the industry's standard dummy text ever</p>
  <p class="lead" style="left:6px;top:160px;width:336px">Lorem Ipsum is simply dummy text of the printing and typesetting industry. Lorem Ipsum has been the industry's standard dummy text ever</p>
  <a class="read-more" href="#" style="left:241px;top:236px">Read more...</a>
</section>

<section class="partners" aria-label="Media partners">
  <span class="partner" style="left:62px">Tamar Times</span>
  <span class="partner" style="left:196px">Southern Shofar</span>
  <span class="partner" style="left:372px">The Kehillah Herald</span>
  <span class="partner" style="left:630px">RootsLedger</span>
  <span class="partner" style="left:846px">The Zion Courier</span>
</section>

<footer>
  <nav class="footer-nav">
    <a href="#" style="left:179px">Home</a>
    <a href="#" style="left:278px">Our mission</a>
    <a href="#" style="left:433px">About Us</a>
    <a href="#" style="left:565px">Personal Media</a>
    <a href="#" style="left:753px">Contact Us</a>
    <a href="#" style="left:895px">On-line Forum</a>
  </nav>
  <p class="copyright">Copyright © 2011. www.lanternmerow.com</p>
  <div class="social">
    <a href="#"><i></i>Kinbook</a>
    <a href="#"><i></i>Chirp</a>
    <a href="#"><i></i>Feed</a>
    <a href="#"><i></i>Workly</a>
    <a href="#"><i></i>Diggin</a>
  </div>
</footer>

</body>
</html>
```